Business Card Design

We need a business card design for a Dry cleaners in Brisbane, Australia. We are trying to promote a fresh/clean image consistent with our website. www.pinnelgarmentcare.com.au

Looking for a professional neat card that's easy to read.

Target Market(s)

Customers looking for a professional, fresh and clean drycleaners.

Industry/Entity Type

Business

Contact Information for Business Card

See our existing business card. The Fax number (07) 3468 5270 to be removed.

Requirements
Must have
• All the details on current business card less the fax number.
Nice to have
• I like white text on coloured background. Blue works well as we are located near the water...

```html
<!DOCTYPE html>
<html lang="en">
<head>
<meta charset="utf-8">
<title>Pinnel Garment Care – Business Card</title>
<link href="https://fonts.googleapis.com/css2?family=Exo+2:wght@400;500;700;800&display=swap" rel="stylesheet">
<style>
  :root {
    --page: #e9eaec;
    --card: #f7f7f8;
    --card-edge: #e2e3e6;
    --navy: #353f92;
    --red: #e83236;
    --ink: #3b3d44;
  }
  * { box-sizing: border-box; margin: 0; padding: 0; }
  html, body { width: 1200px; height: 903px; overflow: hidden; }
  body {
    background: var(--page);
    font-family: "Exo 2", "Segoe UI", sans-serif;
    color: var(--ink);
    position: relative;
  }
  .card {
    position: absolute;
    left: 240px;
    width: 720px;
    height: 411px;
    background: linear-gradient(135deg, #ffffff 0%, var(--card) 55%, #eeeff1 100%);
    border: 1px solid var(--card-edge);
    box-shadow: 0 6px 18px rgba(0,0,0,0.12);
    overflow: hidden;
  }
  .card--back { top: 24px; }
  .card--front { top: 468px; }

  .brand {
    display: flex;
    align-items: center;
    gap: 12px;
    color: var(--navy);
    font-weight: 800;
    letter-spacing: 0.5px;
    white-space: nowrap;
  }
  .brand__mark { background: var(--red); flex: none; }

  .card--back .brand {
    position: absolute;
    left: 50%; top: 50%;
    transform: translate(-50%, -50%);
    font-size: 44px;
  }
  .card--back .brand__mark { width: 22px; height: 22px; }

  .front__accent {
    position: absolute;
    left: 36px; top: 0;
    width: 66px; height: 40px;
    background: var(--red);
  }
  .card--front .brand {
    position: absolute;
    left: 102px; top: 72px;
    font-size: 30px;
  }
  .card--front .brand__mark { width: 16px; height: 16px; }

  .front__band {
    position: absolute;
    left: 394px; right: 0;
    top: 162px; height: 46px;
    background: var(--navy);
  }
  .person {
    position: absolute;
    left: 412px; top: 222px;
  }
  .person__name {
    color: var(--navy);
    font-size: 22px;
    font-weight: 500;
    letter-spacing: 1px;
    text-transform: uppercase;
  }
  .person__role { font-size: 15px; margin-top: 2px; }

  .address {
    position: absolute;
    left: 36px; top: 176px;
    display: flex; gap: 8px;
    font-size: 13.5px;
    line-height: 1.45;
  }
  .contacts {
    position: absolute;
    left: 262px; top: 270px;
    list-style: none;
    font-size: 13.5px;
  }
  .contacts li {
    display: flex; align-items: center; gap: 8px;
    height: 23px;
  }
  .icon { width: 14px; height: 14px; flex: none; fill: var(--red); }
</style>
</head>
<body>

<section class="card card--back" aria-label="Card back">
  <div class="brand"><span class="brand__mark"></span>Pinnel Garment Care</div>
</section>

<section class="card card--front" aria-label="Card front">
  <div class="front__accent"></div>
  <div class="brand"><span class="brand__mark"></span>Pinnel Garment Care</div>
  <div class="front__band"></div>

  <div class="address">
    <svg class="icon" viewBox="0 0 24 24" aria-hidden="true"><path d="M12 2a7 7 0 0 0-7 7c0 5.2 7 13 7 13s7-7.8 7-13a7 7 0 0 0-7-7zm0 9.5A2.5 2.5 0 1 1 12 6.5a2.5 2.5 0 0 1 0 5z"/></svg>
    <p>Shop 4, 212 Wynnum Road<br>Norman Park QLD</p>
  </div>

  <div class="person">
    <p class="person__name">Daniel Whitford</p>
    <p class="person__role">Managing Director</p>
  </div>

  <ul class="contacts">
    <li><svg class="icon" viewBox="0 0 24 24" aria-hidden="true"><path d="M6.6 10.8a15 15 0 0 0 6.6 6.6l2.2-2.2a1 1 0 0 1 1-.25 11.4 11.4 0 0 0 3.6.57 1 1 0 0 1 1 1V20a1 1 0 0 1-1 1A17 17 0 0 1 3 4a1 1 0 0 1 1-1h3.5a1 1 0 0 1 1 1c0 1.25.2 2.45.57 3.6a1 1 0 0 1-.25 1z"/></svg>(07) 3468 5270</li>
    <li><svg class="icon" viewBox="0 0 24 24" aria-hidden="true"><path d="M7 1h10a2 2 0 0 1 2 2v18a2 2 0 0 1-2 2H7a2 2 0 0 1-2-2V3a2 2 0 0 1 2-2zm0 3v14h10V4zm5 15.5a1 1 0 1 0 0 2 1 1 0 0 0 0-2z"/></svg>(07) 3468 5270</li>
    <li><svg class="icon" viewBox="0 0 24 24" aria-hidden="true"><path d="M2 5h20v14H2zm2 2v.5l8 5 8-5V7zm0 3v7h16v-7l-8 5z"/></svg>hello@pinnelgarmentcare.com.au</li>
    <li><svg class="icon" viewBox="0 0 24 24" aria-hidden="true"><path d="M12 2a10 10 0 1 0 0 20 10 10 0 0 0 0-20zm6.9 6h-2.9a15 15 0 0 0-1.4-3.6A8 8 0 0 1 18.9 8zM12 4c.8 1.2 1.5 2.5 1.9 4h-3.8c.4-1.5 1.1-2.8 1.9-4zM4.3 14a8 8 0 0 1 0-4h3.3a16 16 0 0 0 0 4zm.8 2h2.9c.3 1.3.8 2.5 1.4 3.6A8 8 0 0 1 5.1 16zM8 8H5.1a8 8 0 0 1 4.3-3.6C8.8 5.5 8.3 6.7 8 8zm4 12c-.8-1.2-1.5-2.5-1.9-4h3.8c-.4 1.5-1.1 2.8-1.9 4zm2.3-6H9.7a14 14 0 0 1 0-4h4.6a14 14 0 0 1 0 4zm.3 5.6c.6-1.1 1.1-2.3 1.4-3.6h2.9a8 8 0 0 1-4.3 3.6zm1.8-5.6a16 16 0 0 0 0-4h3.3a8 8 0 0 1 0 4z"/></svg>www.pinnelgarmentcare.com.au</li>
  </ul>
</section>

</body>
</html>
```